Company brochure

I would like to redesign our existing brochure.
It shall be trifold brochure with more modern and better appealing design than the old one. I am uploading the old one. The new design shall have all all information repeated from old brochure. It could be more or less pictures. I will provide more pictures if required. The keep text is important, the font shall be more modern. Brochure size shall be trifoldt US Legal size paper 8.5" x 14". I will provide all pitures, logos etc in a original format after design concept will be established or before on request.

Industry/Entity Type

It Company

Font styles to use
Other font styles liked:
• calibri

Colors
0555a3
3176b5
85abd2
0692cd
33a6d7
85cae6
1ab09a
33b8a4
87cfc6

Requirements
Nice to have
• I need all information from existing brochure such as text, customer logos, professional assos. logos to be shown in a new one. Picture could be added more.
Should not have
• No changes allowed to company letterhead. Only slight modifications allowed to company logo

```html
<!DOCTYPE html>
<html lang="en">
<head>
<meta charset="utf-8">
<title>Northfield Cooling &amp; Climate – Trifold Brochure</title>
<link rel="stylesheet" href="https://fonts.googleapis.com/css2?family=Open+Sans:wght@400;600;700&display=swap">
<style>
:root{
  --navy:#0555a3;
  --blue:#3176b5;
  --sky:#85abd2;
  --cyan:#0692cd;
  --cyan-light:#33a6d7;
  --ice:#85cae6;
  --paper:#eef0f3;
  --ink:#3c3f44;
  --bg:#d9dadc;
}
*{margin:0;padding:0;box-sizing:border-box}
html,body{width:1019px;height:1200px;overflow:hidden}
body{background:var(--bg);font-family:"Open Sans",sans-serif;color:var(--ink);position:relative}
.sheet{position:absolute;left:79px;width:866px;height:525px;overflow:hidden;background:var(--paper);box-shadow:0 10px 14px rgba(0,0,0,.25)}
.sheet-outside{top:46px}
.sheet-inside{top:624px}
.abs{position:absolute}
.photo{position:absolute}
.waves{position:absolute;left:0;top:0;width:866px;height:525px}
.text{position:absolute;font-size:8.6px;line-height:10.3px;text-align:justify}
.text p{margin-bottom:8px}
.heading{font-size:11px;font-weight:600;text-transform:uppercase;display:flex;align-items:flex-start;gap:4px;margin-bottom:5px;line-height:14px}
.heading::before{content:"";width:7px;height:7px;margin-top:3px;flex:none;background:var(--cyan-light);border-radius:1px}
.on-blue{color:#fff}
.on-blue .heading{color:#fff}
.on-light .heading{color:var(--cyan)}
.text strong{font-weight:700;color:#222}
.quote-cta{position:absolute;left:289px;width:289px;top:196px;text-align:center;color:var(--cyan);font-size:10.5px;font-weight:600;letter-spacing:.8px}
.contact-btn{position:absolute;left:344px;top:229px;width:177px;height:34px;border-radius:17px;background:linear-gradient(#2a6cbf,var(--navy));color:#fff;font-size:17px;font-weight:600;display:flex;align-items:center;justify-content:center;box-shadow:2px 4px 5px rgba(0,0,0,.3)}
.address{position:absolute;left:289px;width:289px;top:280px;text-align:center;font-size:11px;line-height:14.5px;color:#555}
.phones{position:absolute;left:289px;width:289px;top:313px;display:flex;justify-content:center;gap:8px;font-size:11px;color:#555;align-items:center}
.phones span{display:flex;align-items:center;gap:4px}
.badges{position:absolute;left:300px;top:354px;width:266px;display:flex;justify-content:space-between;align-items:center}
.badge{width:52px;height:40px;background:var(--sky);opacity:.85}
.badge.round{width:40px;border-radius:50%}
.tagline{position:absolute;left:289px;width:289px;top:452px;text-align:center;color:#fff;font-size:9.5px;font-weight:600;letter-spacing:.6px}
.web{position:absolute;top:506px;color:var(--cyan-light);font-size:14px;font-weight:700;letter-spacing:.3px}
.brand{position:absolute;left:622px;top:27px;width:240px;text-align:center;color:#fff;font-size:14px;font-weight:600;font-variant:small-caps;letter-spacing:.5px;line-height:19px}
.services{position:absolute;left:591px;top:417px;list-style:none;color:#fff;font-size:12.3px;line-height:16.3px}
.services li{display:flex;align-items:center;gap:5px}
.services li::before{content:"";width:8px;height:8px;border-radius:50%;background:var(--cyan-light);flex:none}
.circle-photo{position:absolute;border-radius:50%;border:5px solid #fff;box-shadow:0 2px 6px rgba(0,0,0,.35)}
.projects ul{list-style:none}
.projects li{margin-bottom:5px}
.served{position:absolute;right:12px;top:478px;color:#fff;font-size:10.5px;font-weight:600}
.clients{position:absolute;left:0;top:501px;width:866px;height:24px;background:#fff;display:flex;justify-content:space-around;align-items:center;font-size:6.6px;font-weight:700;color:var(--navy);white-space:nowrap}
</style>
</head>
<body>

<section class="sheet sheet-outside">
  <div class="photo" style="left:0;top:0;width:289px;height:135px;background:linear-gradient(135deg,#7d8fa3,#b7c3cf 55%,#5e7690)" role="img" aria-label="Compressor room with blue insulated pipework"></div>
  <div class="photo" style="left:289px;top:0;width:289px;height:145px;background:linear-gradient(160deg,#d6dbe2,#a9b4c1 60%,#c3c9d0)" role="img" aria-label="Rooftop refrigeration piping runs"></div>
  <div class="photo" style="left:578px;top:90px;width:288px;height:320px;background:linear-gradient(150deg,#d9dde0,#6f8a8c 45%,#2f4a4e)" role="img" aria-label="Engine room with teal ammonia compressors"></div>
  <div class="photo" style="left:0;top:395px;width:289px;height:130px;background:linear-gradient(120deg,#7b6a4a,#c29b58 50%,#8c7a5c)" role="img" aria-label="Brass motors and pumps in plant room"></div>

  <svg class="waves" viewBox="0 0 866 525" aria-hidden="true">
    <defs>
      <linearGradient id="gBlue" x1="0" x2="1"><stop offset="0" stop-color="#0a4a94"/><stop offset="1" stop-color="#3176b5"/></linearGradient>
      <linearGradient id="gLight" x1="0" y1="0" x2="0" y2="1"><stop offset="0" stop-color="#f7f8fa"/><stop offset="1" stop-color="#dfe3e8"/></linearGradient>
    </defs>
    <path d="M0,122 C100,130 200,136 289,140 L289,410 L0,410 Z" fill="url(#gBlue)"/>
    <path d="M289,140 C400,143 500,140 578,135 L578,410 L289,410 Z" fill="url(#gLight)"/>
    <path d="M0,110 C200,126 420,138 578,128 L578,140 C420,150 200,140 0,124 Z" fill="var(--cyan-light)"/>
    <path d="M0,106 C200,122 420,134 578,124 L578,129 C420,139 200,127 0,111 Z" fill="#fff"/>
    <path d="M578,0 H866 V84 C780,100 680,130 578,160 Z" fill="url(#gBlue)"/>
    <path d="M578,160 C680,130 780,100 866,84 L866,96 C780,112 680,146 578,176 Z" fill="#fff"/>
    <path d="M289,412 C480,426 700,418 866,370 L866,525 L289,525 Z" fill="url(#gBlue)"/>
    <path d="M0,396 C300,420 600,422 866,358 L866,372 C600,436 300,434 0,410 Z" fill="var(--cyan-light)"/>
    <path d="M0,392 C300,416 600,418 866,354 L866,359 C600,423 300,421 0,397 Z" fill="#fff"/>
  </svg>

  <div class="circle-photo" style="left:749px;top:277px;width:104px;height:104px;background:radial-gradient(circle at 40% 40%,#c9ccd0,#7a8088 70%)" role="img" aria-label="Close-up of a compressor unit"></div>

  <div class="text on-blue" style="left:15px;top:144px;width:260px">
    <h2 class="heading">Refrigeration facilities serviced</h2>
    <p>Food processing, cold storages and distribution facilities, meat and poultry processing plants, bakeries, dairies, beverage bottling facilities, ice production, chemical plants, refineries and ice rinks.</p>
    <h2 class="heading">Industrial &amp; Commercial HVAC<br>facilities serviced</h2>
    <p>Production plant and manufacturing facilities, distribution and storage warehouses, office buildings, data centers, hospitals, colleges, shopping malls and country clubs.</p>
    <h2 class="heading">Construction</h2>
    <p>Ammonia and freon refrigeration build-up systems. Refrigeration and HVAC equipment changeover. Freon packaged condensing units and chillers. Blast freezers, spiral and tunnel freezers. Computerized control, control and power wiring. Build-up glycol and water chillers. Air handlers and evaporators. Refrigeration, glycol, chill water and process piping. Certified X-ray quality welding. Carbon steel, stainless steel, copper, PVC and sanitary piping. Hot tapping available.</p>
  </div>

  <div class="quote-cta">GET A FREE QUOTE &amp; SURVEY</div>
  <div class="contact-btn">CONTACT US</div>
  <div class="address">4410 Cedarline Avenue<br>Harbor Vale, CA 90210</div>
  <div class="phones">
    <span><svg width="12" height="10" viewBox="0 0 12 10" aria-hidden="true"><path d="M1,3 C1,1 3,0 6,0 C9,0 11,1 11,3 L8,4 L8,2.5 L4,2.5 L4,4 Z M2,5 H10 L11,10 H1 Z" fill="var(--navy)"/></svg>555-210-4400</span>
    <span><svg width="11" height="11" viewBox="0 0 11 11" aria-hidden="true"><rect x="2" y="0" width="7" height="4" fill="var(--navy)"/><rect x="0" y="4" width="11" height="7" rx="1" fill="var(--navy)"/><rect x="2" y="6" width="7" height="1.5" fill="#fff"/></svg>555-210-4401</span>
  </div>
  <div class="badges">
    <div class="badge"></div>
    <div class="badge round"></div>
    <div class="badge"></div>
    <div class="badge round" style="width:52px;border-radius:26px/20px"></div>
  </div>

  <div class="brand">Northfield Cooling &amp;<br>Climate</div>
  <ul class="services">
    <li>Industrial &amp; Commercial</li>
    <li>Ammonia &amp; Freon</li>
    <li>Service &amp; Maintenance</li>
    <li>Design &amp; Engineering</li>
    <li>Construction</li>
  </ul>

  <div class="tagline">CUSTOMER SATISFACTION IS OUR ULTIMATE GOAL</div>
  <div class="web" style="right:304px">www.northfieldcool.com</div>
  <div class="web" style="right:9px">www.northfieldcool.com</div>
</section>

<section class="sheet sheet-inside">
  <div class="abs" style="left:0;top:0;width:289px;height:525px;background:linear-gradient(90deg,#f6f7f9,#e6e9ed)"></div>
  <div class="abs" style="left:289px;top:0;width:289px;height:525px;background:linear-gradient(90deg,#dfe3e8,#f4f5f7)"></div>
  <div class="abs" style="left:578px;top:0;width:288px;height:525px;background:linear-gradient(90deg,#e3e6ea,#f5f6f8)"></div>
  <div class="photo" style="left:289px;top:0;width:577px;height:175px;background:linear-gradient(120deg,#2c4d7e,#8ea9c9 45%,#d8e2ee 60%,#3b5c8c)" role="img" aria-label="Technician welding steel pipe with sparks"></div>
  <div class="photo" style="left:0;top:330px;width:578px;height:140px;background:linear-gradient(180deg,rgba(238,240,243,0),#8a9eab 35%,#4f6a78)" role="img" aria-label="Plant floor with rows of compressors and control panels"></div>
  <div class="photo" style="left:720px;top:170px;width:146px;height:245px;background:linear-gradient(90deg,rgba(240,242,245,0),#cfdbe8 40%,#a9bfd6)" role="img" aria-label="Helicopter lifting rooftop equipment over a city skyline"></div>

  <svg class="waves" viewBox="0 0 866 525" aria-hidden="true">
    <defs>
      <linearGradient id="gBlue2" x1="0" x2="1"><stop offset="0" stop-color="#0a4a94"/><stop offset="1" stop-color="#3176b5"/></linearGradient>
    </defs>
    <path d="M289,96 C500,104 700,148 866,176 L866,190 C700,164 500,122 289,112 Z" fill="url(#gBlue2)"/>
    <path d="M289,112 C500,122 700,164 866,190 L866,196 C700,171 500,129 289,118 Z" fill="var(--cyan-light)"/>
    <path d="M289,118 C500,129 700,171 866,196 L866,205 L289,205 Z" fill="#f1f3f5"/>
    <path d="M0,452 C300,470 600,450 866,400 L866,414 C600,464 300,484 0,466 Z" fill="var(--cyan-light)"/>
    <path d="M0,448 C300,466 600,446 866,396 L866,401 C600,451 300,471 0,453 Z" fill="#fff"/>
    <path d="M0,466 C300,484 600,464 866,414 L866,501 L0,501 Z" fill="url(#gBlue2)"/>
  </svg>
  <div class="abs" style="left:289px;top:205px;width:289px;height:125px;background:linear-gradient(90deg,#e3e7eb,#f4f5f7)"></div>

  <div class="circle-photo" style="left:305px;top:1px;width:90px;height:90px;background:linear-gradient(135deg,#c8d0d8,#6e7c8a)" role="img" aria-label="Evaporative condenser unit"></div>

  <div class="text on-light" style="left:15px;top:31px;width:260px">
    <h2 class="heading">Service and maintenance</h2>
    <p><strong>24 hour Emergency Service</strong><br>Ammonia and Freon. Customized maintenance program. Troubleshooting service and repair of refrigeration and HVAC systems including all mechanical, structural, electrical and control components. Compressor rebuilding as well as vibration and oil analysis. Refrigerant conversion and recovery.</p>
    <p>Build-up ammonia and freon refrigeration systems, packaged freon refrigeration units, blast freezing/cooling systems, spiral and tunnel freezers, holding freezers and coolers, evaporators, glycol and water chillers, ice production machines, process rooms.</p>
    <p>Compressors, evaporative and air-cool condensers, recirculation packages, ammonia, water and glycol pumps, heat exchangers, control valves and regulators, electrical motors. Safety devices test, repair and calibration including: relief valves, leak detectors, pressure and temperature sensors, level switches and interlock devices.</p>
    <p>Packaged and split gas/electric air conditioners, heat pumps. Air handlers, exhaust fans, swamp coolers, water chillers, water towers and pumps. Exhaust and ventilation, humidification and dehumidification, clean rooms. Boilers and Boiler Piping. Refrigeration and Building Control and automation. PLC, VFD, VSD, VAV.</p>
  </div>

  <div class="text on-light" style="left:304px;top:120px;width:260px">
    <h2 class="heading">Experience</h2>
    <p>Thirty plus years in industrial, commercial, ammonia and freon refrigeration and air conditioning. Experienced in all aspects of refrigeration projects, from design concept through execution, with the ability to cost-effectively satisfy customer requirements within aggressive time frames.</p>
    <h2 class="heading" style="margin-top:12px">Engineering services</h2>
    <p>Design ammonia and freon systems. Build-up and packaged refrigeration systems. Liquid recirculating, flooded, and DX systems. Low and high temperature chillers. Glycol and chill water distribution systems.<br>Energy saving and expansion projects. 3D solid modeling and CAD drawings. Computerized control design and implementation, PLC, VFD. Mechanical integrity surveys, safety and hazard analysis, seismic assessment. Safety programs, PSM, RMP, CalARP, MOC, SOP. Regulatory Compliance and Professional training.</p>
  </div>

  <div class="text on-light projects" style="left:594px;top:207px;width:184px">
    <h2 class="heading">Major projects completed</h2>
    <ul>
      <li>• <strong>675 TR, 1960 HP</strong> ammonia refrigeration system for a bakery.</li>
      <li>• <strong>90 TR, 400 HP</strong> freon spiral blast freezer for meat processing plant.</li>
      <li>• <strong>920 TR, 1420 HP</strong> ammonia refrigeration system for meat processing facility.</li>
      <li>• <strong>1300 TR</strong> freon chiller and glycol chiller and glycol distribution system for a dairy processing plant.</li>
      <li>• An ammonia refrigeration system for 560,000 sq. ft cold storage and food distribution facility.</li>
      <li>• 480 ton ice production facility.</li>
      <li>• <strong>375 TR, 1500 HP</strong> ice-cream plant.</li>
    </ul>
  </div>

  <div class="served">COMPANIES WE PROUDLY SERVE</div>
  <div class="clients">
    <span>Valley Dairy</span><span>BulkMart</span><span>Trailhead Co</span><span>Hillside Hospital</span><span>Fizz Cola</span><span>Meadow Foods</span><span>Oakbarn</span><span>Sunridge</span><span>Coastline Aero</span><span>Cake House</span><span>Artisan Bakes</span><span>Bakery Group</span><span>Greenway Fresh</span><span>Coldstore</span><span>Mesa Market</span><span>Frostline</span><span>Nordmill</span>
  </div>
</section>

</body>
</html>
```